Business Card Design

We are a company that provides stump grinding services for residential and commercial clients. Looking for a simple business card design that may have some type of graphic on the card that will tie in with the Tamsen name(Grizzly Bear, Paw Print, etc) . Possibly some foliage wrapping around part of the card? Would like to have a simple design that stands out because it is unique. We are working on getting the website set up and there is a simple graphic on the top of the page that came to mind when I mentioned the leaves.

Industry/Entity Type

Business

Contact Information for Business Card

Tamsen Stump Grinding 303-257-4788KodiakStumps.Com

Font styles to use
Serif

Requirements
Must have
• Business name
• Website Address
• Phone Number
Nice to have
• Graphics that would be associated with a Tamsen bear.
Should not have
• Nothing frilly

```html
<!DOCTYPE html>
<html lang="en">
<head>
<meta charset="utf-8">
<title>Tamsen Stump Grinding – Business Card</title>
<link rel="stylesheet" href="https://fonts.googleapis.com/css2?family=Montserrat:wght@500&family=Open+Sans:wght@400&display=swap">
<style>
  :root {
    --page-bg: #e9e7e4;
    --card-dark: #2a2a2b;
    --card-light: #ffffff;
    --brand-blue: #4a86c8;
    --brand-blue-light: #6aa3dc;
    --steel-dark: #3a3a3c;
    --steel-light: #a9a9ab;
    --text-grey: #555658;
    --text-white: #f4f4f4;
  }
  html, body {
    margin: 0;
    width: 1200px;
    height: 900px;
    overflow: hidden;
    background: var(--page-bg);
  }
  .canvas {
    position: relative;
    width: 1200px;
    height: 900px;
  }
  .card {
    position: absolute;
    left: 250px;
    width: 700px;
    height: 400px;
    overflow: hidden;
    box-shadow: 0 6px 18px rgba(0,0,0,0.18);
  }
  .card--front { top: 40px; background: var(--card-dark); }
  .card--back  { top: 470px; background: var(--card-light); }

  .wordmark {
    position: absolute;
    display: flex;
    align-items: center;
    gap: 16px;
  }
  .wordmark__dot {
    width: 72px;
    height: 72px;
    border-radius: 50%;
    flex: none;
  }
  .wordmark__name {
    font-family: "Montserrat", sans-serif;
    font-weight: 500;
    font-size: 30px;
    line-height: 1.15;
    text-transform: uppercase;
    letter-spacing: 0.02em;
    margin: 0;
  }
  .wordmark__name span { display: block; letter-spacing: 0.55em; font-size: 18px; }

  .card--front .wordmark { left: 180px; top: 152px; }
  .card--front .wordmark__dot { background: var(--text-white); }
  .card--front .wordmark__name { color: var(--text-white); }

  .card--back .wordmark { left: 300px; top: 160px; }
  .card--back .wordmark__dot { background: var(--brand-blue); }
  .card--back .wordmark__name { color: var(--brand-blue); }

  .card__decor { position: absolute; left: 0; top: 0; }

  .contact {
    position: absolute;
    left: 72px;
    top: 44px;
    margin: 0;
    padding: 0;
    list-style: none;
    font-family: "Open Sans", sans-serif;
    font-size: 19px;
    color: var(--text-grey);
  }
  .contact__item {
    display: flex;
    align-items: center;
    gap: 10px;
    height: 28px;
  }
  .contact__icon { width: 16px; height: 16px; flex: none; }
</style>
</head>
<body>
<main class="canvas">

  <section class="card card--front" aria-label="Card front">
    <div class="wordmark">
      <div class="wordmark__dot"></div>
      <h1 class="wordmark__name">Tamsen Stump <span>Grinding</span></h1>
    </div>
  </section>

  <section class="card card--back" aria-label="Card back">
    <svg class="card__decor" width="700" height="400" viewBox="0 0 700 400" aria-hidden="true">
      <defs>
        <linearGradient id="blueBand" x1="0" x2="1" y1="0" y2="0">
          <stop offset="0" stop-color="var(--brand-blue)"/>
          <stop offset="1" stop-color="var(--brand-blue-light)"/>
        </linearGradient>
        <linearGradient id="steelBand" x1="0" x2="1" y1="0" y2="0">
          <stop offset="0" stop-color="var(--steel-dark)"/>
          <stop offset="1" stop-color="var(--steel-light)"/>
        </linearGradient>
      </defs>
      <!-- top corner tab -->
      <polygon points="0,40 18,40 0,70" fill="var(--brand-blue)"/>
      <polygon points="28,40 58,40 30,88 0,88 0,82" fill="var(--steel-dark)"/>
      <!-- bottom bands -->
      <polygon points="0,284 302,318 296,330 0,300" fill="url(#blueBand)"/>
      <polygon points="305,330 700,372 700,400 0,400 0,400 290,345" fill="url(#steelBand)"/>
      <polygon points="310,318 700,360 700,372 304,330" fill="var(--card-light)"/>
    </svg>

    <ul class="contact">
      <li class="contact__item">
        <svg class="contact__icon" viewBox="0 0 16 16" aria-hidden="true">
          <path d="M2 6c0-2 2-3 6-3s6 1 6 3v1h-3V5.5H5V7H2z" fill="var(--brand-blue)"/>
          <rect x="4" y="8" width="8" height="6" rx="1" fill="var(--brand-blue)"/>
        </svg>
        <span>303-555-0146</span>
      </li>
      <li class="contact__item">
        <svg class="contact__icon" viewBox="0 0 16 16" aria-hidden="true">
          <path d="M6.5 9.5l3-3M7 4.5l1.5-1.5a2.5 2.5 0 013.5 3.5L10.5 8M9 11.5L7.5 13a2.5 2.5 0 01-3.5-3.5L5.5 8" fill="none" stroke="var(--brand-blue)" stroke-width="1.6" stroke-linecap="round"/>
        </svg>
        <span>TamsenStumps.Com</span>
      </li>
    </ul>

    <div class="wordmark">
      <div class="wordmark__dot"></div>
      <p class="wordmark__name">Tamsen Stump <span>Grinding</span></p>
    </div>
  </section>

</main>
</body>
</html>
```